Business Card Design for a Personal Trainer

I need a business card design for my job as a personal trainer. It should have a unique, modern and exclusive design. On the front there should be only my logo with my name and my job. 0162/3819204 Tobias Lendhart Wiesengrundweg 14 80417 Munich Germany The most important contact information is the web adress. it can be bigger than the rest, but its not necessary. The card should be 8,5cmx5,5cm big. Font: Roboto. Colors: black, white, gray, 56c1ff.

```html
<!DOCTYPE html>
<html lang="de">
<head>
<meta charset="utf-8">
<title>Tobias Lendhart – Visitenkarte</title>
<link href="https://fonts.googleapis.com/css2?family=Roboto:wght@300;400;700&display=swap" rel="stylesheet">
<style>
  :root {
    --page: #4a4a4c;
    --card-logo: #232324;
    --card-contact: #252526;
    --ink-dark: #3c3c3e;
    --white: #ffffff;
    --gray: #cfcfcf;
    --accent: #56c1ff;
    --photo-top: #5a5a5c;
    --photo-bottom: #1e1e1f;
  }
  html, body {
    margin: 0;
    width: 1200px;
    height: 1021px;
    overflow: hidden;
    background: var(--page);
    font-family: "Roboto", sans-serif;
  }
  .stage { position: relative; width: 1200px; height: 1021px; }
  .card {
    position: absolute;
    width: 640px;
    height: 414px;
    border-radius: 4px;
    box-shadow: 0 12px 30px rgba(0,0,0,.45);
    overflow: hidden;
  }
  .card--logo {
    left: 420px; top: 64px;
    background: var(--card-logo);
    display: flex; flex-direction: column; align-items: center; justify-content: center;
  }
  .card--logo .brand-name {
    font-size: 46px; font-weight: 400; letter-spacing: 2px;
    text-transform: uppercase; color: var(--ink-dark);
  }
  .card--logo .brand-role {
    margin-top: 8px; font-size: 16px; font-weight: 400; letter-spacing: 8px;
    text-transform: uppercase; color: var(--ink-dark);
  }
  .card--contact {
    left: 140px; top: 543px;
    background: var(--card-contact);
  }
  .contact-block {
    position: absolute; left: 34px; top: 52px; width: 340px;
    text-align: center; color: var(--white);
  }
  .contact-block .brand-name {
    font-size: 34px; font-weight: 400; letter-spacing: 1px;
    text-transform: uppercase; color: var(--white);
  }
  .contact-block .brand-role {
    margin-top: 4px; font-size: 12px; letter-spacing: 7px;
    text-transform: uppercase; color: var(--white);
  }
  .website {
    margin-top: 20px; font-size: 27px; font-weight: 700; color: var(--accent);
  }
  .details { margin-top: 18px; font-size: 19px; font-weight: 400; line-height: 1.3; color: var(--gray); }
  .divider { width: 70px; height: 2px; background: var(--accent); margin: 12px auto; }
  .trainer-photo {
    position: absolute; right: 40px; bottom: 0; width: 250px; height: 330px;
    background: linear-gradient(180deg, var(--photo-top), var(--photo-bottom));
    border-radius: 120px 120px 0 0;
  }
</style>
</head>
<body>
<main class="stage">
  <section class="card card--logo">
    <div class="brand-name">Tobias Lendhart</div>
    <div class="brand-role">Personal Trainer</div>
  </section>

  <section class="card card--contact">
    <div class="contact-block">
      <div class="brand-name">Tobias Lendhart</div>
      <div class="brand-role">Personal Trainer</div>
      <div class="website">www.lendhart-training.de</div>
      <div class="details">
        <div>0162/3819204</div>
        <div>t.lendhart@mailbox.de</div>
        <div class="divider"></div>
        <div>Wiesengrundweg 14</div>
        <div>80417 München</div>
      </div>
    </div>
    <div class="trainer-photo" role="img" aria-label="Black and white portrait of the trainer with crossed arms, wearing a long-sleeve sports shirt"></div>
  </section>
</main>
</body>
</html>
```